A new presentation to our clients

we are a Real Estate agency, our website is www.lumibrasa.com and it’s time to have a new, fashion and remarcable Business Card. we want to differentiate ourselves from other companies so we want a business card that differentiates us. we want the business card to impact our customers. in the competitive market that we have today, we have to be different and it is this difference that we seek

Target Market(s)

Real Estate Clients

Contact Information for Business Card

We search a totaly diferent card from the usual

Font styles to use
Sans Serif

Colors
e34197

Requirements
Must have
• Logo, adress, phone contact, e-mail, photo, and our website
Nice to have
• We would like to see a modern business card
Should not have
• Houses or building draws

```html
<!DOCTYPE html>
<html lang="en">
<head>
<meta charset="utf-8">
<title>Lumi Brasa — Business Card</title>
<link rel="stylesheet" href="https://fonts.googleapis.com/css2?family=Open+Sans:wght@400;600;700&display=swap">
<style>
  :root {
    --stage: #3b3b3e;
    --card: #1f2022;
    --card-edge: #26272a;
    --brand-pink: #e34197;
    --text-grey: #b9b9bc;
    --rule: #4a4b4f;
    --silver: #d6d6d9;
  }
  * { margin: 0; padding: 0; box-sizing: border-box; }
  html, body {
    width: 1200px; height: 1108px; overflow: hidden;
    background: var(--stage);
    font-family: "Open Sans", Arial, sans-serif;
  }
  .stage {
    position: relative; width: 1200px; height: 1108px;
    display: flex; justify-content: center; align-items: center; gap: 90px;
  }
  .card {
    position: relative; width: 380px; height: 590px;
    background: var(--card); border-radius: 22px;
    box-shadow: 0 18px 40px rgba(0,0,0,.45);
    overflow: hidden;
  }
  /* Front */
  .card-front { display: flex; flex-direction: column; align-items: center; text-align: center; }
  .brand-name {
    font-weight: 600; color: var(--brand-pink);
    font-size: 50px; letter-spacing: 1px; margin-top: 170px; line-height: 1;
  }
  .person { margin-top: 78px; }
  .person-name { color: var(--brand-pink); font-weight: 700; font-size: 19px; letter-spacing: .3px; }
  .person-role { color: var(--text-grey); font-size: 16px; margin-top: 1px; }
  .rule { width: 220px; height: 1px; background: var(--rule); margin: 10px 0; }
  .contact-icons { display: flex; gap: 5px; }
  .contact-icons svg { width: 20px; height: 20px; display: block; }
  .contact-list { list-style: none; color: var(--text-grey); font-size: 17px; line-height: 1.28; margin-top: 6px; }
  .address { color: var(--text-grey); font-size: 17px; line-height: 1.28; font-style: normal; }
  /* Back */
  .brand-pattern {
    position: absolute; inset: 0;
    background: linear-gradient(150deg, #26272a 0%, #222326 45%, #1f2022 100%);
  }
  .brand-name-back {
    position: absolute; left: 0; right: 0; bottom: 70px; text-align: center;
    font-weight: 600; color: var(--silver); font-size: 54px; letter-spacing: 1px;
  }
</style>
</head>
<body>
<main class="stage">
  <section class="card card-front" aria-label="Card front">
    <div class="brand-name">Lumi Brasa</div>
    <div class="person">
      <div class="person-name">DANIEL MOREIRA</div>
      <div class="person-role">Managing Director</div>
    </div>
    <div class="rule"></div>
    <div class="contact-icons">
      <svg viewBox="0 0 20 20" aria-label="Phone"><rect width="20" height="20" fill="var(--brand-pink)"/><path d="M6 5h3l1 3-2 1a7 7 0 0 0 3 3l1-2 3 1v3c-6 0-9-3-9-9z" fill="#fff"/></svg>
      <svg viewBox="0 0 20 20" aria-label="Fax"><rect width="20" height="20" fill="var(--brand-pink)"/><rect x="6" y="4" width="8" height="4" fill="#fff"/><rect x="4" y="8" width="12" height="5" fill="#fff"/><rect x="6" y="12" width="8" height="4" fill="#fff" stroke="var(--brand-pink)"/></svg>
      <svg viewBox="0 0 20 20" aria-label="Email"><rect width="20" height="20" fill="var(--brand-pink)"/><rect x="4" y="6" width="12" height="8" fill="#fff"/><path d="M4 6l6 5 6-5" fill="none" stroke="var(--brand-pink)" stroke-width="1.2"/></svg>
      <svg viewBox="0 0 20 20" aria-label="Website"><rect width="20" height="20" fill="var(--brand-pink)"/><circle cx="10" cy="10" r="6" fill="#fff"/><path d="M4 10h12M10 4c-3 3-3 9 0 12M10 4c3 3 3 9 0 12" fill="none" stroke="var(--brand-pink)" stroke-width="1"/></svg>
    </div>
    <ul class="contact-list">
      <li>(+351) 210 448 360</li>
      <li>(+351) 210 448 369</li>
      <li>geral@lumibrasa.com</li>
      <li>www.lumibrasa.com</li>
    </ul>
    <div class="rule"></div>
    <address class="address">Rua das Flores, 118<br>4050-262, Porto</address>
  </section>

  <section class="card card-back" aria-label="Card back">
    <div class="brand-pattern" role="img" aria-label="Faint repeated brand name pattern across the card"></div>
    <div class="brand-name-back">Lumi Brasa</div>
  </section>
</main>
</body>
</html>
```